Copper Lantern

Need a business card for our restaurant. Restaurant and Bar in the mountains of North Idaho. Rustic looking card

rustic design, wood and metal looking, primarily neutral colors

• Name, address, phone number, website, email address

```html
<!DOCTYPE html>
<html lang="en">
<head>
<meta charset="utf-8">
<title>Copper Lantern – Business Card</title>
<link href="https://fonts.googleapis.com/css2?family=Montserrat:wght@400;700&display=swap" rel="stylesheet">
<style>
  :root {
    --backdrop: #3a3a3a;
    --card-black: #161616;
    --ink-white: #ffffff;
    --ink-black: #111111;
    --muted-white: #e8e8e8;
  }
  * { margin: 0; padding: 0; box-sizing: border-box; }
  html, body {
    width: 1200px;
    height: 689px;
    overflow: hidden;
    background: var(--backdrop);
    font-family: "Montserrat", sans-serif;
  }
  .canvas {
    position: relative;
    width: 1200px;
    height: 689px;
  }
  .card {
    position: absolute;
    top: 190px;
    width: 540px;
    height: 309px;
    border-radius: 22px;
    background: var(--card-black);
    overflow: hidden;
  }
  .card--back { left: 40px; }
  .card--front { left: 620px; }

  .brand-name {
    font-family: "Montserrat", sans-serif;
    font-weight: 400;
    text-transform: uppercase;
    letter-spacing: 4px;
    font-size: 24px;
    text-align: center;
    line-height: 1.3;
  }
  .card--back .brand {
    position: absolute;
    inset: 0;
    display: flex;
    align-items: center;
    justify-content: center;
    gap: 16px;
    color: var(--ink-white);
  }
  .brand-dot {
    width: 10px;
    height: 10px;
    border-radius: 50%;
    background: var(--ink-white);
  }

  .front-circle {
    position: absolute;
    left: 285px;
    top: -40px;
    width: 290px;
    height: 290px;
    border-radius: 50%;
    background: var(--ink-white);
    display: flex;
    align-items: center;
    justify-content: center;
    color: var(--ink-black);
  }
  .front-circle .brand-name { font-size: 22px; }

  .contact {
    position: absolute;
    left: 32px;
    top: 112px;
    bottom: 20px;
    display: flex;
    flex-direction: column;
    color: var(--ink-white);
  }
  .contact__name {
    font-weight: 700;
    font-size: 25px;
    line-height: 1.2;
    letter-spacing: 0.3px;
  }
  .contact__role {
    font-size: 13px;
    color: var(--muted-white);
    margin-top: 2px;
  }
  .contact__address {
    font-size: 13px;
    line-height: 1.45;
    color: var(--muted-white);
    margin-top: 20px;
  }
  .contact__lines {
    list-style: none;
    margin-top: auto;
    font-size: 12.5px;
    color: var(--muted-white);
  }
  .contact__lines li {
    display: flex;
    align-items: center;
    gap: 8px;
    line-height: 1.55;
  }
  .contact__lines svg { width: 11px; height: 11px; fill: var(--ink-white); flex: none; }
</style>
</head>
<body>
<main class="canvas">

  <section class="card card--back" aria-label="Card back">
    <div class="brand">
      <span class="brand-dot"></span>
      <p class="brand-name">Copper Lantern<br>Restaurant and Bar</p>
    </div>
  </section>

  <section class="card card--front" aria-label="Card front">
    <div class="front-circle">
      <p class="brand-name">Copper<br>Lantern</p>
    </div>

    <div class="contact">
      <h1 class="contact__name">Owen Hartley</h1>
      <p class="contact__role">Managing Director</p>
      <p class="contact__address">Your address, City<br>State, Zip 1234</p>
      <ul class="contact__lines">
        <li>
          <svg viewBox="0 0 24 24" aria-hidden="true"><path d="M6.6 10.8a15 15 0 0 0 6.6 6.6l2.2-2.2a1 1 0 0 1 1-.25 11.4 11.4 0 0 0 3.6.57 1 1 0 0 1 1 1V20a1 1 0 0 1-1 1A17 17 0 0 1 3 4a1 1 0 0 1 1-1h3.5a1 1 0 0 1 1 1c0 1.250.2 2.45.57 3.57a1 1 0 0 1-.25 1z"/></svg>
          123 456 789
        </li>
        <li>
          <svg viewBox="0 0 24 24" aria-hidden="true"><path d="M2 5h20v14H2z M4 7v.5l8 5 8-5V7l-8 5z" fill-rule="evenodd"/></svg>
          info@yourgmail.com
        </li>
        <li>
          <svg viewBox="0 0 24 24" aria-hidden="true"><circle cx="12" cy="12" r="10"/></svg>
          www.yourwebsite.com
        </li>
      </ul>
    </div>
  </section>

</main>
</body>
</html>
```